Interior Design/ New Construction interior finishes

Interior Design Website

Target Market(s)

Home builders, New Construction, Renovations, Public

Industry/Entity Type

Construction

Coding

Coded - Design and coding required

Number of Pages Required

1 page

Font styles to use
Sans Serif

Colors

Designer to choose colors to be used in the design.

Requirements
Must have
• Section to upload pictures of projects
• Simple and modern design
• Designer 1 details about myself
• Logo
• Upload section for photos for future jobs
Nice to have
• Sections they can click on to see certain rooms in a house
• Decorating, floral arrangements, holiday decorating.
• I have lots of before and after as well. Maybe a section for those.

```html
<!DOCTYPE html>
<html lang="en">
<head>
<meta charset="utf-8">
<title>Loma Interiors — Interior Design</title>
<link href="https://fonts.googleapis.com/css2?family=Lato:ital,wght@0,300;0,400;0,700;1,400&display=swap" rel="stylesheet">
<style>
:root{
  --ink:#222;
  --text:#555;
  --muted:#777;
  --blue:#1f5fa8;
  --bar:#2f2f2f;
  --soft:#f0f0f0;
  --white:#fff;
  --footer:#2a2623;
  --footer-text:#cfc8c0;
}
*{margin:0;padding:0;box-sizing:border-box}
html,body{width:1200px;height:3364px;overflow:hidden}
body{font-family:'Lato',sans-serif;color:var(--text);background:var(--white);position:relative}
.abs{position:absolute}
section,header,footer{position:absolute;left:0;width:1200px}

/* top bar */
.topbar{top:0;height:47px;background:var(--bar);color:#eee;font-size:13px}
.topbar .socials{left:78px;top:14px;display:flex;gap:14px}
.dot{width:18px;height:18px;border-radius:50%;background:#ddd;display:block}
.topbar .contact{right:74px;top:0;height:47px;display:flex;align-items:center;gap:28px}
.topbar .contact span{display:flex;align-items:center;gap:10px}

/* nav */
.nav{top:47px;height:90px;background:var(--white)}
.nav ul{list-style:none;display:flex;gap:34px;position:absolute;top:44px;font-size:12px;font-weight:700;letter-spacing:.3px;color:var(--ink)}
.nav .left{left:76px}
.nav .right{right:74px}
.nav .active{color:var(--blue)}
.brand-mark{left:558px;top:-30px;width:84px;height:84px;border-radius:50%;background:var(--white);border:4px solid var(--ink)}
.brand-name{left:0;width:1200px;text-align:center;top:58px;font-size:22px;letter-spacing:2px;color:var(--ink);font-weight:400}

/* hero */
.hero{top:137px;height:523px;background:linear-gradient(120deg,#6d5a48 0%,#a58a6c 35%,#cfc3b3 60%,#8b7763 100%)}
.hero h1{position:absolute;left:0;width:1200px;text-align:center;color:var(--white);font-weight:700;text-shadow:0 2px 6px rgba(0,0,0,.4)}
.hero .pre{top:196px;font-size:44px;font-weight:700;letter-spacing:1px}
.hero .main{top:240px;font-size:74px;letter-spacing:1px}
.arrow{position:absolute}

/* headings */
.h-light{font-weight:300;color:#333;line-height:1.12}
.center{text-align:center;width:1200px;left:0}

/* about */
.about{top:660px;height:340px}
.about h2{left:76px;top:38px;font-size:50px}
.about p{left:76px;top:166px;width:594px;font-size:13.5px;line-height:26px}
.about .mark{left:825px;top:50px;width:180px;height:180px;border-radius:50%;border:7px solid var(--ink)}
.about .name{left:700px;width:430px;text-align:center;top:240px;font-size:56px;color:var(--ink);letter-spacing:3px}

/* what we do */
.what{top:1000px;height:380px;background:var(--soft)}
.card{top:34px;width:243px;height:305px;background:var(--white);text-align:center;padding:28px 24px 0}
.card h3{color:var(--blue);font-size:18px;font-weight:400;line-height:24px;margin-top:14px}
.card p{font-size:13px;line-height:23px;margin-top:6px}
.what h2{left:615px;top:68px;font-size:50px}
.what p.body{left:615px;top:186px;width:510px;font-size:13.5px;line-height:25px}

/* specialized */
.special{top:1380px;height:505px}
.special h2{top:40px;font-size:50px}
.tile{top:123px;width:332px}
.tile .img{height:208px}
.tile h3{text-align:center;font-size:22px;font-weight:400;color:#222;margin-top:22px}
.tile p{text-align:center;font-size:13.5px;line-height:22px;margin-top:6px;padding:0 24px}

/* before after */
.ba{top:1885px;height:347px;background:var(--soft)}
.ba h2{left:72px;top:38px;font-size:50px}
.ba h3{left:76px;top:122px;font-size:27px;font-weight:400;color:#222}
.ba p{left:76px;top:170px;width:390px;font-size:13.5px;line-height:25px}
.ba .link{left:76px;top:274px;font-size:13px;font-weight:700;color:var(--blue);text-decoration:underline}
.ba .shot{top:51px;width:273px;height:229px}
.ba .cap{top:292px;width:273px;text-align:center;font-size:15px;color:#333}

/* testimonials */
.testi{top:2232px;height:325px}
.testi h2{top:44px;font-size:50px}
.quote{top:126px;width:320px;text-align:center}
.quote svg{display:block;margin:0 auto}
.quote p{font-style:italic;font-size:13px;line-height:23px;margin-top:18px}
.quote .who{font-style:normal;color:var(--blue);font-weight:700;margin-top:14px;font-size:13px}

/* gallery */
.gallery{top:2557px;height:550px;background:var(--soft)}
.gallery h2{top:50px;font-size:50px}
.grid{left:74px;top:141px;width:1052px;height:350px;display:grid;grid-template-columns:260px 249px 247px 260px;grid-template-rows:171px 168px;column-gap:12px;row-gap:11px}
.tall{grid-row:1 / span 2}

/* footer */
.footer{top:3107px;height:257px;background:var(--footer);color:var(--footer-text);font-size:14px}
.footer h4{color:var(--white);font-size:15px;font-weight:700;letter-spacing:.5px}
.footer .fmark{left:116px;top:46px;width:54px;height:54px;border-radius:50%;border:3px solid var(--white)}
.footer .fname{left:60px;width:170px;text-align:center;top:108px;color:var(--white);font-size:20px;letter-spacing:1.5px}
.footer .copy{left:74px;top:154px;font-size:11px;line-height:17px}
.footer ul{list-style:none;line-height:31px}
.footer .c-line{display:flex;align-items:center;gap:14px}
</style>
</head>
<body>

<header class="topbar">
  <div class="abs socials" aria-label="Social links">
    <span class="dot"></span><span class="dot"></span><span class="dot"></span><span class="dot"></span><span class="dot"></span>
  </div>
  <div class="abs contact">
    <span><svg width="13" height="13" viewBox="0 0 24 24"><path fill="#eee" d="M6.6 10.8a15.1 15.1 0 0 0 6.6 6.6l2.2-2.2c.3-.3.7-.4 1-.2 1.1.4 2.3.6 3.6.6.6 0 1 .4 1 1V20c0 .6-.4 1-1 1A17 17 0 0 1 3 4c0-.6.4-1 1-1h3.5c.6 0 1 .4 1 1 0 1.3.2 2.5.6 3.6.1.3 0 .7-.2 1z"/></svg>1-800-555-0142</span>
    <span><svg width="14" height="11" viewBox="0 0 24 18"><rect width="24" height="18" rx="2" fill="#eee"/><path d="M1 1l11 9 11-9" stroke="#2f2f2f" stroke-width="2" fill="none"/></svg>hello@lomainteriors.com</span>
  </div>
</header>

<nav class="nav">
  <ul class="left"><li class="active">HOME</li><li>WHO WE ARE</li><li>WHAT WE DO</li><li>PROJECTS</li></ul>
  <div class="abs brand-mark"></div>
  <div class="abs brand-name">Loma Interiors</div>
  <ul class="right"><li>BLOG</li><li>TESTIMONIALS</li><li>CAREERS</li><li>CONTACT US</li></ul>
</nav>

<section class="hero" role="img" aria-label="Photo of an open-plan kitchen and dining room with a round wooden table and staircase">
  <svg class="arrow" style="left:62px;top:243px" width="22" height="40" viewBox="0 0 22 40"><path d="M19 2L3 20l16 18" stroke="#fff" stroke-width="3" fill="none"/></svg>
  <svg class="arrow" style="left:1116px;top:243px" width="22" height="40" viewBox="0 0 22 40"><path d="M3 2l16 18L3 38" stroke="#fff" stroke-width="3" fill="none"/></svg>
  <h1 class="pre">WELCOME TO</h1>
  <h1 class="main">LOMA INTERIORS</h1>
</section>

<section class="about">
  <h2 class="abs h-light">About<br>Loma Interiors</h2>
  <p class="abs">Aliquam molestie, mi et imperdiet euismod, dui purus auctor tellus, et interdum lacus lectus et ante. Sed accumsan sollicitudin sapien, sit amet adipiscing turpis gravida ac. In congue, neque ac lobortis volutpat, libero mauris varius mi, vitae suscipit ipsum ligula vitae risus. Duis aliquam nibh a dui iaculis viverra id a velit. Vivamus egestas risus in magna varius commodo. Sed semper viverra egestas.</p>
  <div class="abs mark"></div>
  <div class="abs name">Loma Interiors</div>
</section>

<section class="what">
  <div class="abs card" style="left:74px">
    <svg width="90" height="78" viewBox="0 0 90 78"><rect x="6" y="38" width="50" height="22" rx="4" fill="#111"/><rect x="2" y="30" width="12" height="30" rx="4" fill="#111"/><rect x="48" y="30" width="12" height="30" rx="4" fill="#111"/><rect x="10" y="60" width="4" height="8" fill="#111"/><rect x="48" y="60" width="4" height="8" fill="#111"/><path d="M64 4h20l-4 14H68z" fill="#111"/><rect x="73" y="18" width="2" height="48" fill="#111"/><rect x="66" y="66" width="16" height="3" fill="#111"/></svg>
    <h3>INTERIOR<br>DECORATION</h3>
    <p>Aliquam molestie, mi et imperdiet euismod, dui purus auctor tellus, et interdum lacus lectus et ante.</p>
  </div>
  <div class="abs card" style="left:345px">
    <svg width="90" height="78" viewBox="0 0 90 78" fill="#111"><rect x="18" y="40" width="24" height="10"/><rect x="46" y="40" width="24" height="10"/><rect x="10" y="54" width="24" height="10"/><rect x="38" y="54" width="24" height="10"/><rect x="66" y="54" width="14" height="10"/><rect x="18" y="68" width="24" height="10"/><rect x="46" y="68" width="24" height="10"/><rect x="30" y="6" width="30" height="10" rx="3"/><rect x="34" y="18" width="22" height="18"/></svg>
    <h3>CONSTRUCTION<br>SERVICES</h3>
    <p>Aliquam molestie, mi et imperdiet euismod, dui purus auctor tellus, et interdum lacus lectus et ante.</p>
  </div>
  <h2 class="abs h-light">What<br>We Do</h2>
  <p class="abs body">Aliquam molestie, mi et imperdiet euismod, dui purus auctor tellus, et interdum lacus lectus et ante. Sed accumsan sollicitudin sapien, sit amet adipiscing turpis gravida ac. In congue, neque ac lobortis volutpat, libero mauris varius mi, vitae suscipit ipsum ligula vitae risus. Duis aliquam nibh a dui iaculis viverra id a velit.</p>
</section>

<section class="special">
  <h2 class="abs center h-light">We Specialized</h2>
  <div class="abs tile" style="left:74px">
    <div class="img" role="img" aria-label="Photo of a decorated dining area with round table and chairs" style="background:linear-gradient(135deg,#8a6a4c,#c9a57c 55%,#6f7d86)"></div>
    <h3>Feature Decorating</h3>
    <p>Aliquam molestie, mi et imperdiet euismod, dui purus auctor tellus, et interdum lacus lectus et ante.</p>
  </div>
  <div class="abs tile" style="left:435px">
    <div class="img" role="img" aria-label="Photo of a workspace with a floral wall mural and mint chairs" style="background:linear-gradient(135deg,#3b3d3f,#8f8c86 50%,#c9ccc4)"></div>
    <h3>Floral Arrangements</h3>
    <p>Aliquam molestie, mi et imperdiet euismod, dui purus auctor tellus, et interdum lacus lectus et ante.</p>
  </div>
  <div class="abs tile" style="left:794px">
    <div class="img" role="img" aria-label="Photo of a holiday-decorated room with red cushions and white furniture" style="background:linear-gradient(135deg,#c98d78,#e9d6c8 55%,#b8303a)"></div>
    <h3>Holiday Decorating</h3>
    <p>Aliquam molestie, mi et imperdiet euismod, dui purus auctor tellus, et interdum lacus lectus et ante.</p>
  </div>
</section>

<section class="ba">
  <h2 class="abs h-light">Before &amp; After</h2>
  <h3 class="abs">Project Name</h3>
  <p class="abs">Sed accumsan sollicitudin sapien, sit amet adipiscing turpis gravida ac. In congue, neque ac lobortis volutpat, libero mauris varius mi..</p>
  <div class="abs link">VIEW ALL WORK</div>
  <svg class="arrow" style="left:483px;top:160px" width="12" height="20" viewBox="0 0 12 20"><path d="M10 2L2 10l8 8" stroke="#666" stroke-width="2.5" fill="none"/></svg>
  <div class="abs shot" style="left:523px" role="img" aria-label="Before photo of a gutted room full of rubble" style="background:#7a6f63"></div>
  <div class="abs shot" style="left:523px;background:linear-gradient(135deg,#5e5449,#9b8f80 50%,#6b6258)" role="img" aria-label="Before photo of a gutted room full of rubble"></div>
  <div class="abs shot" style="left:814px;background:linear-gradient(135deg,#5d6a6e,#d9dcd8 50%,#f2f2ef)" role="img" aria-label="After photo of a bright renovated kitchen with glass roof"></div>
  <div class="abs cap" style="left:523px">Before</div>
  <div class="abs cap" style="left:814px">After</div>
  <svg class="arrow" style="left:1113px;top:160px" width="12" height="20" viewBox="0 0 12 20"><path d="M2 2l8 8-8 8" stroke="#666" stroke-width="2.5" fill="none"/></svg>
</section>

<section class="testi">
  <h2 class="abs center h-light">Customer Tesimonials</h2>
  <div class="abs quote" style="left:80px">
    <svg width="38" height="30" viewBox="0 0 38 30" fill="#1f5fa8"><path d="M0 0h16v16l-6 14H3l5-14H0zM22 0h16v16l-6 14h-7l5-14h-8z"/></svg>
    <p>Sed accumsan sollicitudin sapien, sit amet adipiscing turpis gravida ac. In congue, neque ac lobortis volutpat, libero mauris varius mi..</p>
    <p class="who">-Name Heading</p>
  </div>
  <div class="abs quote" style="left:440px">
    <svg width="38" height="30" viewBox="0 0 38 30" fill="#1f5fa8"><path d="M0 0h16v16l-6 14H3l5-14H0zM22 0h16v16l-6 14h-7l5-14h-8z"/></svg>
    <p>Sed accumsan sollicitudin sapien, sit amet adipiscing turpis gravida ac. In congue, neque ac lobortis volutpat, libero mauris varius mi..</p>
    <p class="who">-Name Heading</p>
  </div>
  <div class="abs quote" style="left:800px">
    <svg width="38" height="30" viewBox="0 0 38 30" fill="#1f5fa8"><path d="M0 0h16v16l-6 14H3l5-14H0zM22 0h16v16l-6 14h-7l5-14h-8z"/></svg>
    <p>Sed accumsan sollicitudin sapien, sit amet adipiscing turpis gravida ac. In congue, neque ac lobortis volutpat, libero mauris varius mi..</p>
    <p class="who">-Name Heading</p>
  </div>
</section>

<section class="gallery">
  <h2 class="abs center h-light">Gallery</h2>
  <div class="abs grid">
    <div role="img" aria-label="Photo of a white kitchen with dark countertops" style="background:linear-gradient(135deg,#e6e4df,#9a958d)"></div>
    <div class="tall" role="img" aria-label="Photo of a dining room with chandelier and upholstered chairs" style="background:linear-gradient(180deg,#b79a72,#e1dbd2 45%,#8a7f72)"></div>
    <div class="tall" role="img" aria-label="Photo of a console table with mirror and flowers" style="background:linear-gradient(180deg,#c9bba6,#ece6dc 50%,#6e6254)"></div>
    <div role="img" aria-label="Photo of a bedroom with tray ceiling" style="background:linear-gradient(135deg,#c4ab8d,#8b6f55)"></div>
    <div role="img" aria-label="Photo of a modern living space with red rug" style="background:linear-gradient(135deg,#2c2b2b,#6a6663 55%,#9d1c22)"></div>
    <div role="img" aria-label="Photo of a warm wood-beamed dining room" style="background:linear-gradient(135deg,#7a4a2a,#c88c5a 50%,#4a3020)"></div>
  </div>
</section>

<footer class="footer">
  <div class="abs fmark"></div>
  <div class="abs fname">Loma Interiors</div>
  <div class="abs copy">Copyright © 2018. Loma Interiors.<br>All Right Reserved</div>

  <h4 class="abs" style="left:343px;top:45px">SITE MAP</h4>
  <ul class="abs" style="left:343px;top:70px"><li>Home</li><li>Who We Are</li><li>What We Do</li><li>Project</li></ul>
  <ul class="abs" style="left:476px;top:70px"><li>Blog</li><li>Testimonials</li><li>Contact Us</li></ul>

  <h4 class="abs" style="left:619px;top:45px">CONTACT INFO</h4>
  <div class="abs" style="left:619px;top:76px;color:#fff;font-weight:700;font-size:15px">Loma Interiors</div>
  <div class="abs" style="left:619px;top:106px;line-height:22px">120 Alder Lane,<br>Brookfield, BF2 7QA</div>
  <div class="abs c-line" style="left:619px;top:158px"><svg width="13" height="13" viewBox="0 0 24 24"><path fill="#cfc8c0" d="M6.6 10.8a15.1 15.1 0 0 0 6.6 6.6l2.2-2.2c.3-.3.7-.4 1-.2 1.1.4 2.3.6 3.6.6.6 0 1 .4 1 1V20c0 .6-.4 1-1 1A17 17 0 0 1 3 4c0-.6.4-1 1-1h3.5c.6 0 1 .4 1 1 0 1.3.2 2.5.6 3.6.1.3 0 .7-.2 1z"/></svg>1-800-555-0142</div>
  <div class="abs c-line" style="left:619px;top:187px"><svg width="14" height="11" viewBox="0 0 24 18"><rect width="24" height="18" rx="2" fill="#cfc8c0"/><path d="M1 1l11 9 11-9" stroke="#2a2623" stroke-width="2" fill="none"/></svg>hello@lomainteriors.com</div>

  <h4 class="abs" style="left:886px;top:45px">FOLLOW US</h4>
  <div class="abs" style="left:886px;top:82px;display:flex;gap:17px" aria-label="Social links">
    <span class="dot" style="background:#eee"></span><span class="dot" style="background:#eee"></span><span class="dot" style="background:#eee"></span><span class="dot" style="background:#eee"></span><span class="dot" style="background:#eee"></span>
  </div>
</footer>

</body>
</html>
```